We need 3 A2 posters similar look but different enough to be eye catching when changed.

We are a healthcare centre that requires 3 A2 posters - simple, similar but different background colours. These posters will be used within our business to promote services we provide to our clients.

The design should include our logo(attached), a large header and a large section in the middle of the poster to promote the event. We need a blank text box (which WE can insert text to advertise), and 1 image to advertise the event. Please note, we do not need you to choose an image we simply would like you to place a demo to give us an idea of where it should sit.

We want to use the bubble design (attached) as a background and the company colours pink, orange and blue - as on our website. Attached is a copy of our logo and background bubble effect. You can also refer to our website - www.tallowbrookwellness.com.au for more inspiration.

Just to reiterate, these posters should be simple, different but have a uniform feel. They should have an empty middle section that can be edited to add text and a space for an eye catching title and matching image.

Our services include Chiropractic, Podiatry, Nutrition, Massage, Yoga, Pilates and Specialised rehabilitation classes.

Reason: Hi designers, I know we are all busy but I really need more designs from the designers I invited to this project and look forward to receiving more designs. Any questions please let me know. Regards, Marion

Reason: Hi all Increased the budget Regards Marion

Corporate Sydney City office workers

Healthcare

• logo and company colours
section in the middles that can be edited to add text
Space allocated for image placement
Catchy title/header

```html
<!DOCTYPE html>
<html lang="en">
<head>
<meta charset="utf-8">
<title>Tallowbrook Wellness – Poster</title>
<link rel="stylesheet" href="https://fonts.googleapis.com/css2?family=Poppins:wght@600;700&display=swap">
<style>
  :root {
    --pink: #c43be2;
    --pink-soft: rgba(196, 59, 226, 0.5);
    --orange: #d89243;
    --blue: #5e83f2;
    --white: #ffffff;
    --photo-sky: #d9eef5;
    --photo-skin: #f1c9b6;
  }
  * { margin: 0; padding: 0; box-sizing: border-box; }
  html, body {
    width: 916px;
    height: 1200px;
    overflow: hidden;
    background: var(--white);
  }
  .poster {
    position: relative;
    width: 916px;
    height: 1200px;
    background: var(--white);
    font-family: "Poppins", sans-serif;
    overflow: hidden;
  }

  /* Top brand band */
  .brand-band {
    position: absolute;
    top: 0; left: 0;
    width: 916px; height: 81px;
    display: flex;
  }
  .brand-band .band-pink { width: 196px; background: var(--pink); }
  .brand-band .band-orange { width: 83px; background: var(--orange); }
  .brand-band .band-blue { flex: 1; background: var(--blue); }
  .brand-name {
    position: absolute;
    left: 24px; top: 36px;
    font-size: 28px;
    font-weight: 700;
    color: var(--white);
    letter-spacing: -0.3px;
    line-height: 1;
  }
  .pointer {
    position: absolute;
    left: 113px; top: 88px;
  }

  /* Decorative squares */
  .tile {
    position: absolute;
    background: var(--pink-soft);
    border-radius: 4px;
  }

  /* Headline */
  .headline {
    position: absolute;
    left: 214px; top: 128px;
    font-size: 92px;
    font-weight: 600;
    line-height: 86px;
    color: var(--pink);
    letter-spacing: -1px;
  }

  /* Content frame */
  .content-frame {
    position: absolute;
    left: 67px; top: 451px;
    width: 786px; height: 701px;
    border: 7px solid var(--pink);
    border-radius: 20px;
    background: var(--white);
    box-shadow: 10px 14px 24px rgba(40, 110, 130, 0.22);
  }
  .event-photo {
    position: absolute;
    left: 247px; top: 351px;
    width: 632px; height: 276px;
    border: 5px solid var(--pink);
    border-radius: 16px;
    background: linear-gradient(100deg, var(--photo-skin) 0%, var(--photo-sky) 45%, var(--photo-skin) 100%);
    box-shadow: 10px 16px 26px rgba(40, 110, 130, 0.28);
  }
  .intro {
    position: absolute;
    left: 102px; top: 710px;
    width: 700px;
    font-size: 22px;
    font-weight: 600;
    line-height: 30px;
    color: var(--pink);
  }
  .intro p + p { margin-top: 30px; }

  /* Bottom band */
  .footer-band {
    position: absolute;
    left: 0; bottom: 0;
    width: 916px; height: 21px;
    display: flex;
  }
  .footer-band .band-blue { width: 636px; background: var(--blue); }
  .footer-band .band-orange { width: 83px; background: var(--orange); }
  .footer-band .band-pink { flex: 1; background: var(--pink); }
</style>
</head>
<body>
<main class="poster">
  <header class="brand-band">
    <div class="band-pink"></div>
    <div class="band-orange"></div>
    <div class="band-blue"></div>
  </header>
  <div class="brand-name">Tallowbrook Wellness</div>
  <svg class="pointer" width="83" height="67" viewBox="0 0 83 67" aria-hidden="true">
    <polygon points="0,0 83,0 41.5,67" fill="#c43be2"/>
  </svg>

  <div class="tile" style="left:47px;top:193px;width:61px;height:36px"></div>
  <div class="tile" style="left:20px;top:209px;width:67px;height:43px"></div>
  <div class="tile" style="left:47px;top:223px;width:83px;height:54px"></div>
  <div class="tile" style="left:71px;top:267px;width:111px;height:71px"></div>
  <div class="tile" style="left:23px;top:295px;width:119px;height:78px"></div>
  <div class="tile" style="left:74px;top:322px;width:148px;height:97px"></div>

  <h1 class="headline">Header text<br>space</h1>

  <section class="content-frame"></section>
  <div class="event-photo" role="img" aria-label="Event photo placeholder: relaxed client receiving a treatment"></div>

  <div class="intro">
    <p>Welcome to Tallowbrook Wellness. Our goal is to achieve the best possible health outcome for our patients. Our unique combination of therapies, structural correction and individualised exercise programs is what sets us apart.</p>
    <p>At anytime, if you have a health condition, even if you feel it is not something we could help you with, contact us and we will find the right solution for you. We are here for the health of our community"</p>
  </div>

  <footer class="footer-band">
    <div class="band-blue"></div>
    <div class="band-orange"></div>
    <div class="band-pink"></div>
  </footer>
</main>
</body>
</html>
```